Road Construction Company needs business cards

We would like a new business card designed for our business.

We're a road construction company based in Qld, Australia.

Can the business card please have the following information on it.

Name: Warren Halbeck
Position: General Manager
Phone: 0472 915 348
Email: Warren.halbeck@tovrin.com.au
Address: 87 Marrow Ave, Pendlebay, QLD, 4023
Website: www.tovrin.com.au

Visually we'd like the card to be professional and simple.

Attached is our logo.

Our website is www.tovrin.com.au

Target Market(s)

Men aged 25-60

Contact Information for Business Card

As listed in project description

Font styles to use
Serif

Requirements
Must have
• Large logo on back of card

```html
<!DOCTYPE html>
<html lang="en">
<head>
<meta charset="utf-8">
<title>Tovrin Business Card</title>
<link href="https://fonts.googleapis.com/css2?family=Inter:wght@400;600;800&display=swap" rel="stylesheet">
<style>
  :root {
    --backdrop: #9a9a9a;
    --card: #181818;
    --emboss: #2b2b2b;
    --brand-blue: #0f5fb5;
    --name-blue: #2fa4dc;
    --icon-blue: #1b74c4;
    --text: #ececec;
    --band-start: #0a5fb0;
    --band-end: #2ea3d8;
  }
  * { margin: 0; padding: 0; box-sizing: border-box; }
  html, body {
    width: 1200px; height: 588px; overflow: hidden;
    background: var(--backdrop);
    font-family: "Inter", Arial, sans-serif;
  }
  .card {
    position: absolute;
    top: 142px;
    width: 486px; height: 287px;
    background: var(--card);
    overflow: hidden;
  }
  .card--back { left: 87px; }
  .card--front { left: 622px; }

  .back-wordmark {
    position: absolute; left: 0; right: 0; top: 108px;
    text-align: center;
    font-weight: 800; font-size: 58px; letter-spacing: 1px;
    color: var(--emboss); line-height: 1;
  }

  .front-wordmark {
    position: absolute; left: 27px; top: 122px;
    font-weight: 800; font-size: 37px; letter-spacing: 0.5px;
    color: var(--brand-blue); line-height: 1;
  }
  .divider {
    position: absolute; left: 246px; top: 69px;
    width: 1px; height: 149px; background: var(--name-blue);
  }
  .details {
    position: absolute; left: 258px; top: 66px;
    color: var(--text);
  }
  .details__name {
    font-weight: 600; font-size: 18px; color: var(--name-blue);
    line-height: 22px; letter-spacing: 0.2px;
  }
  .details__role { font-size: 13.5px; line-height: 18px; }
  .details__address { margin-top: 13px; font-size: 13.5px; line-height: 18px; }
  .details__contact { margin-top: 14px; list-style: none; font-size: 13.5px; line-height: 18px; }
  .details__contact li { display: flex; align-items: center; gap: 5px; }
  .details__contact svg { width: 10px; height: 10px; fill: var(--icon-blue); flex: none; }
  .accent-band {
    position: absolute; left: 0; right: 0; bottom: 0; height: 11px;
    background: linear-gradient(90deg, var(--band-start), var(--band-end));
  }
</style>
</head>
<body>
  <section class="card card--back">
    <div class="back-wordmark">TOVRIN</div>
  </section>

  <section class="card card--front">
    <div class="front-wordmark">TOVRIN</div>
    <div class="divider"></div>
    <div class="details">
      <p class="details__name">WARREN HALBECK</p>
      <p class="details__role">General Manager</p>
      <p class="details__address">87 Marrow Ave<br>Pendlebay, QLD, 4023</p>
      <ul class="details__contact">
        <li>
          <svg viewBox="0 0 24 24" aria-hidden="true"><path d="M6.6 10.8a15.1 15.1 0 0 0 6.6 6.6l2.2-2.2c.3-.3.7-.4 1-.2 1.1.4 2.3.6 3.6.6.6 0 1 .4 1 1V20c0 .6-.4 1-1 1A17 17 0 0 1 3 4c0-.6.4-1 1-1h3.5c.6 0 1 .4 1 1 0 1.3.2 2.5.6 3.6.1.3 0 .7-.2 1z"/></svg>
          0472 915 348
        </li>
        <li>
          <svg viewBox="0 0 24 24" aria-hidden="true"><path d="M2 5h20v14H2z M2 5l10 7 10-7" /><path d="M2 6.5l10 7 10-7V5H2z" fill="#0d3f75"/></svg>
          Warren.halbeck@tovrin.com.au
        </li>
        <li>
          <svg viewBox="0 0 24 24" aria-hidden="true"><circle cx="12" cy="12" r="10"/><path d="M2 12h20M12 2c3 3 3 17 0 20M12 2c-3 3-3 17 0 20" stroke="#181818" stroke-width="1.5" fill="none"/></svg>
          www.tovrin.com.au
        </li>
      </ul>
    </div>
    <div class="accent-band"></div>
  </section>
</body>
</html>
```